Business card for Luxury Portable Restroom Trailer company

We are a Luxury Portable Restroom Trailer Company Called FALCRIDGE HIRES. Based in Orange County California. We provide portable restroom trailers for events, such as, Weddings, Concerts, Charity events, Sporting events, Tournaments, Corporate events, ect. We rent and Sell the Luxury restrooms. Our colors are white, grey, and Orange. As you will see in the logo we uploaded.
There are 2 people in the company so the names and titles will change for the 3 people but card will remain the same. Here is the information for each Person: Dwight Penner CFO 555 318-0476
next Person: Leon Marchetti VP 555 318-0476
Next Person: Owen Marchetti CEO 555 318-0476
Information to include on the card: Luxury Restroom Trailers Rental and Sales. Weddings, Concerts, Charity, Sporting and Corp. Events.

```html
<!DOCTYPE html>
<html lang="en">
<head>
<meta charset="utf-8">
<title>Falcridge Hires — Business Card</title>
<link rel="stylesheet" href="https://fonts.googleapis.com/css2?family=Montserrat:wght@400;500;600;700;800&display=swap">
<style>
  :root {
    --page: #1c1c1e;
    --card: #262627;
    --card-back: #222223;
    --orange: #f26a21;
    --white: #f4f4f4;
    --grey: #c9c9c9;
    --pattern: #2e2e30;
  }
  * { box-sizing: border-box; margin: 0; padding: 0; }
  html, body { width: 1200px; height: 801px; overflow: hidden; }
  body {
    background: var(--page);
    font-family: "Montserrat", sans-serif;
    display: flex;
    align-items: center;
    justify-content: center;
    gap: 40px;
  }
  .card {
    width: 540px;
    height: 309px;
    position: relative;
    border-bottom: 4px solid var(--orange);
    overflow: hidden;
  }
  .card-front { background: var(--card); }
  .card-back { background: var(--card-back); }

  .brand {
    position: absolute;
    left: 34px;
    top: 108px;
    width: 200px;
    text-align: center;
  }
  .brand-name {
    color: var(--white);
    font-weight: 800;
    font-size: 25px;
    line-height: 1.05;
    letter-spacing: 1px;
  }
  .divider {
    position: absolute;
    left: 262px;
    top: 40px;
    width: 1px;
    height: 134px;
    background: var(--orange);
  }
  .person {
    position: absolute;
    left: 286px;
    top: 38px;
  }
  .person-name {
    color: var(--orange);
    font-weight: 700;
    font-size: 22px;
    letter-spacing: 0.5px;
    text-transform: uppercase;
  }
  .person-title {
    color: var(--white);
    font-size: 13px;
    margin-top: 2px;
  }
  .contacts {
    list-style: none;
    margin-top: 16px;
  }
  .contacts li {
    display: flex;
    align-items: center;
    gap: 8px;
    color: var(--white);
    font-size: 12.5px;
    margin-bottom: 6px;
  }
  .contacts svg { width: 11px; height: 11px; flex: none; }
  .tagline {
    position: absolute;
    left: 0;
    right: 0;
    bottom: 30px;
    text-align: center;
  }
  .tagline-service {
    color: var(--orange);
    font-weight: 500;
    font-size: 14px;
  }
  .tagline-events {
    color: var(--white);
    font-size: 15px;
    margin-top: 4px;
    letter-spacing: 0.3px;
  }

  .back-pattern {
    position: absolute;
    inset: 0;
    background: radial-gradient(ellipse at 70% 30%, #3a3a3c 0%, var(--pattern) 45%, var(--card-back) 100%);
  }
  .back-mark {
    position: absolute;
    right: 70px;
    top: 150px;
    display: flex;
    align-items: center;
    gap: 10px;
  }
  .back-mark .dot {
    width: 34px;
    height: 34px;
    border: 3px solid var(--orange);
    border-radius: 50%;
  }
  .back-mark span {
    color: var(--orange);
    font-weight: 800;
    font-size: 15px;
    letter-spacing: 1px;
  }
</style>
</head>
<body>
  <section class="card card-front">
    <div class="brand">
      <p class="brand-name">FALCRIDGE<br>HIRES</p>
    </div>
    <div class="divider"></div>
    <div class="person">
      <h1 class="person-name">Owen Marchetti</h1>
      <p class="person-title">CEO</p>
      <ul class="contacts">
        <li>
          <svg viewBox="0 0 12 12"><path d="M3 1l2 2.5-1.2 1.3a7 7 0 0 0 3.4 3.4L8.5 7 11 9l-1 2C5 11 1 7 1 2z" fill="#f26a21"/></svg>
          555 318-0476
        </li>
        <li>
          <svg viewBox="0 0 12 12"><rect x="1" y="2.5" width="10" height="7" rx="1" fill="#f26a21"/><path d="M1.5 3l4.5 3.5L10.5 3" stroke="#262627" fill="none"/></svg>
          owen@falcridgehires.com
        </li>
        <li>
          <svg viewBox="0 0 12 12"><circle cx="6" cy="6" r="5" fill="#f26a21"/><path d="M1 6h10M6 1c-2 2.5-2 7.5 0 10M6 1c2 2.5 2 7.5 0 10" stroke="#262627" stroke-width="0.8" fill="none"/></svg>
          www.falcridgehires.com
        </li>
      </ul>
    </div>
    <div class="tagline">
      <p class="tagline-service">Luxury Restroom Trailers Rental and Sales</p>
      <p class="tagline-events">Weddings | Concerts | Charity | Sporting | Corp</p>
    </div>
  </section>

  <section class="card card-back">
    <div class="back-pattern" role="img" aria-label="Repeating pattern of the company's circular emblem in dark grey tones"></div>
    <div class="back-mark">
      <div class="dot"></div>
      <span>FALCRIDGE HIRES</span>
    </div>
  </section>
</body>
</html>
```